Animal Eye Clinic needs a Business card

We are a new veterinary ophthalmology practice (Ridgeline Pet Vision Care) and we need a business card designed. We only see animal eyes - we are not a regular veterinary clinic. We already have a logo. We are looking for a professional, good looking business card to hand out to our clients. We are looking for something simple but professional and contemporary. Our logo is likely the only picture/graphic that needs to be on the card.
Updates

Contact Information for Business Card

Delia Vossman, BSc, DVM, MSc, DipACVO
Veterinary Ophthalmologist

Phone: 250.418.3927
Email: ridgelinepetvisioncare@mailbox-example.net
Website: ridgelinepetvisioncare-example.net
Address: 1874 Thornbury Rd
Kelowna, BC, V1X 4M9

Colors

Designer to choose colors to be used in the design.

Requirements
Must have
• Our logo (attached)

```html
<!DOCTYPE html>
<html lang="en">
<head>
<meta charset="utf-8">
<title>Ridgeline Pet Vision Care – Business Card</title>
<link href="https://fonts.googleapis.com/css2?family=Roboto:wght@300;400;500;700&display=swap" rel="stylesheet">
<style>
  :root {
    --bg: #3a3a3c;
    --card: #2a2a2b;
    --card-edge: #323234;
    --teal: #0a9aa8;
    --text: #e9e9e9;
    --muted: #bdbdbd;
    --rule: #cfcfcf;
  }
  * { margin: 0; padding: 0; box-sizing: border-box; }
  html, body { width: 1200px; height: 901px; overflow: hidden; }
  body {
    background: var(--bg);
    font-family: "Roboto", Arial, sans-serif;
    color: var(--text);
    position: relative;
  }
  .card {
    position: absolute;
    left: 220px;
    width: 760px;
    height: 420px;
    background: radial-gradient(ellipse at 80% 45%, var(--card-edge) 0%, var(--card) 60%);
    overflow: hidden;
    box-shadow: 0 10px 30px rgba(0,0,0,.45);
  }
  .card--front { top: 20px; }
  .card--back { top: 461px; }

  .brand { display: flex; align-items: center; gap: 16px; }
  .brand__dot {
    width: 46px; height: 46px; border-radius: 50%;
    background: var(--teal); flex: none;
  }
  .brand__name {
    color: var(--teal);
    font-weight: 500;
    text-transform: uppercase;
    letter-spacing: 2px;
    line-height: 1.15;
  }
  .card--front .brand {
    position: absolute; left: 170px; top: 160px;
  }
  .card--front .brand__name { font-size: 34px; }
  .card--front .brand__dot { width: 62px; height: 62px; }

  .card--back .brand {
    position: absolute; left: 40px; top: 150px; width: 270px;
  }
  .card--back .brand__name { font-size: 22px; }

  .divider {
    position: absolute; left: 325px; top: 70px;
    width: 1px; height: 240px; background: var(--rule);
  }
  .contact {
    position: absolute; left: 352px; top: 66px; right: 20px;
    font-size: 18px; font-weight: 300; line-height: 1.3;
  }
  .contact__name { color: var(--teal); font-weight: 500; font-size: 19px; }
  .contact__creds { color: var(--teal); font-size: 12px; font-weight: 400; }
  .contact__role { margin-bottom: 14px; }
  .contact__address { margin-bottom: 14px; }
  .contact__line { display: flex; align-items: center; gap: 8px; font-size: 17px; }
  .contact__line svg { width: 14px; height: 14px; flex: none; fill: var(--teal); }
  .contact__web span { color: var(--teal); }

  .band {
    position: absolute; left: 0; right: 0; bottom: 0;
    height: 14px; background: var(--teal);
  }
</style>
</head>
<body>

<section class="card card--front" aria-label="Business card front">
  <div class="brand">
    <span class="brand__dot"></span>
    <div class="brand__name">Ridgeline Pet<br>Vision Care</div>
  </div>
</section>

<section class="card card--back" aria-label="Business card back">
  <div class="brand">
    <span class="brand__dot"></span>
    <div class="brand__name">Ridgeline Pet<br>Vision Care</div>
  </div>

  <div class="divider"></div>

  <div class="contact">
    <div><span class="contact__name">Delia Vossman</span><span class="contact__creds">, BSc, DVM, MSc, DipACVO</span></div>
    <div class="contact__role">Veterinary Ophthalmologist</div>
    <div class="contact__address">1874 Thornbury Rd<br>Kelowna, BC, V1X 4M9</div>
    <div class="contact__line">
      <svg viewBox="0 0 24 24" aria-hidden="true"><path d="M6.6 10.8a15.1 15.1 0 0 0 6.6 6.6l2.2-2.2c.3-.3.7-.4 1-.2 1.1.4 2.3.6 3.6.6.6 0 1 .4 1 1V20c0 .6-.4 1-1 1C10.6 21 3 13.4 3 4c0-.6.4-1 1-1h3.5c.6 0 1 .4 1 1 0 1.3.2 2.5.6 3.6.1.3 0 .7-.2 1z"/></svg>
      250.418.3927
    </div>
    <div class="contact__line">
      <svg viewBox="0 0 24 24" aria-hidden="true"><path d="M2 5h20v14H2z M3.5 6.5 12 13l8.5-6.5" fill="none" stroke="#0a9aa8" stroke-width="2"/></svg>
      ridgelinepetvisioncare@mailbox-example.net
    </div>
    <div class="contact__line contact__web">
      <svg viewBox="0 0 24 24" aria-hidden="true"><circle cx="12" cy="12" r="9" fill="none" stroke="#0a9aa8" stroke-width="2"/><path d="M3 12h18M12 3c3 3 3 15 0 18M12 3c-3 3-3 15 0 18" fill="none" stroke="#0a9aa8" stroke-width="1.6"/></svg>
      <div>www.<span>ridgelinepetvisioncare-example</span>.net</div>
    </div>
  </div>

  <div class="band"></div>
</section>

</body>
</html>
```